Simple and Clean business card design

We would like the design to be simple clean and to incorporate our colors.

We are open to your design and talent, we have the dots in our logo as we think of it as data points and we connect data points for people.

We are open to see the great creative and clean design you bring to the table

Contact Information for Business Card

please include: name, position, email, phone and website

Font styles to use
Sans Serif

Requirements
Must have
• my colors incorporated, simplicity
Nice to have
• lots of white space, simplicity
Should not have
• complexicity/ complex art

```html
<!DOCTYPE html>
<html lang="en">
<head>
<meta charset="utf-8">
<title>Bramble business card</title>
<link rel="stylesheet" href="https://fonts.googleapis.com/css2?family=Poppins:wght@400;500;600&display=swap">
<style>
  :root {
    --backdrop: #e9e7e3;
    --card: #ffffff;
    --ink: #1c1c1e;
    --muted: #5a5a5f;
    --rule: #3a5bb0;
    --blue: #3f6fc4;
    --green: #2e9d4a;
    --yellow: #e3a72a;
    --red: #d9392b;
  }
  * { margin: 0; padding: 0; box-sizing: border-box; }
  html, body { width: 807px; height: 1200px; overflow: hidden; }
  body {
    background: var(--backdrop);
    font-family: "Poppins", sans-serif;
    color: var(--ink);
    position: relative;
  }
  .card {
    position: absolute;
    left: 93px;
    width: 620px;
    height: 354px;
    background: var(--card);
    border-radius: 10px;
    box-shadow: 0 10px 30px rgba(0,0,0,0.12);
    overflow: hidden;
  }
  .card--front { top: 170px; }
  .card--back { top: 676px; }

  .wordmark {
    position: absolute;
    left: 0; right: 0; top: 0; bottom: 0;
    display: flex; align-items: center; justify-content: center; gap: 14px;
  }
  .wordmark__dot {
    width: 22px; height: 22px; border-radius: 50%;
    background: var(--green);
  }
  .wordmark__name {
    font-size: 72px; font-weight: 600; letter-spacing: -1px;
    color: var(--ink);
  }

  .accent {
    position: absolute; left: 38px; top: 150px;
  }

  .contact {
    position: absolute; left: 318px; top: 150px; width: 260px;
  }
  .contact__name {
    font-size: 20px; font-weight: 600; letter-spacing: 0.5px; text-transform: uppercase;
  }
  .contact__role {
    font-size: 12px; color: var(--muted); margin-top: 2px;
  }
  .contact__rule {
    height: 1px; background: var(--rule); margin: 10px 0 12px; width: 240px;
  }
  .contact__list { list-style: none; }
  .contact__item {
    display: flex; align-items: center; gap: 8px;
    font-size: 11.5px; color: var(--muted); margin-bottom: 5px;
  }
  .contact__item svg { width: 11px; height: 11px; flex: none; }
</style>
</head>
<body>
  <section class="card card--front" aria-label="Card front">
    <div class="wordmark">
      <span class="wordmark__name">Bramble</span>
      <span class="wordmark__dot"></span>
    </div>
  </section>

  <section class="card card--back" aria-label="Card back">
    <svg class="accent" width="120" height="120" viewBox="0 0 120 120" aria-hidden="true">
      <circle cx="60" cy="60" r="50" fill="var(--blue)" opacity="0.9"/>
    </svg>

    <div class="contact">
      <h1 class="contact__name">Daniel Reyes</h1>
      <p class="contact__role">Founder/ CEO</p>
      <div class="contact__rule"></div>
      <ul class="contact__list">
        <li class="contact__item">
          <svg viewBox="0 0 12 12" aria-hidden="true"><path d="M3 1h2l1 3-1.5 1a6 6 0 0 0 2.5 2.5L8 6l3 1v2a1.5 1.5 0 0 1-1.5 1.5A8.5 8.5 0 0 1 1.5 2.5 1.5 1.5 0 0 1 3 1z" fill="var(--red)"/></svg>
          555-014-2270
        </li>
        <li class="contact__item">
          <svg viewBox="0 0 12 12" aria-hidden="true"><rect x="1" y="2.5" width="10" height="7" rx="1" fill="var(--red)"/><path d="M1.5 3.5 6 6.5l4.5-3" stroke="#fff" stroke-width="1" fill="none"/></svg>
          daniel.reyes@bramble.one
        </li>
        <li class="contact__item">
          <svg viewBox="0 0 12 12" aria-hidden="true"><circle cx="6" cy="6" r="5" fill="var(--green)"/><path d="M1 6h10M6 1c2 2 2 8 0 10M6 1c-2 2-2 8 0 10" stroke="#fff" stroke-width="0.8" fill="none"/></svg>
          www.Bramble.one
        </li>
      </ul>
    </div>
  </section>
</body>
</html>
```